Refresh Velquor Web Presence - www.velquor-sample.com

Velquor (www.velquor-sample.com)web site needs a makeover. It needs to be more modern, less cluttered, more corporate, prestigious, user friendly, impressive, up to date. We want a modern corporate image that encourages our business users to trust us and buy our products and services. They need to understand that they are dealing with a highly reputable, long established company, but one that is up to date and forward thinking.
1. Clean uncluttered design.
2. Domain Registration box and Countries (price) box to be collapsible and expandable.
3. All links on page need to be conserved for SEO but hidden from view.
4. Logo and general colour scheme need to be retained.
5. Phone number to be prominently displayed at top of page.
6. No calls to action (CTA) below the fold.
7. Sites we like: www.brinzal-sample.com, www.tundexa-sample.com,www.qop.com,www.plavion-sample.com, www.fismet-sample.com (busy but clear CTAs), www.yarmel-sample.com
Reason: We lost a lot of time to review over the holiday weekend. We need to have a chance to interact during business hours.
Target Market(s)
Small business to large enterprise
Industry/Entity Type
Business
Look and feel

```html
<!DOCTYPE html>
<html lang="en">
<head>
<meta charset="utf-8">
<title>Velquor — Com.AU</title>
<link rel="stylesheet" href="https://fonts.googleapis.com/css2?family=Oswald:wght@300;400&family=Ubuntu:wght@400;500;700&display=swap">
<style>
:root{
  --page:#f6f6f6;
  --ink:#333333;
  --body:#4a4a4a;
  --rule:#c9c9c9;
  --orange:#e8730f;
  --orange-light:#f7962a;
  --navy:#2d3190;
  --navy-light:#4c52b5;
  --band:#efefef;
  --footer-top:#1c1c1c;
  --footer-bottom:#000000;
  --footer-text:#d8d8d8;
  --footer-dash:#555555;
  --badge:#9a9a9a;
}
*{margin:0;padding:0;box-sizing:border-box}
html,body{width:1200px;height:874px;overflow:hidden}
body{position:relative;background:var(--page);font-family:"Ubuntu",sans-serif;color:var(--body)}
.abs{position:absolute}
.heading{font-family:"Oswald",sans-serif;font-weight:400}

/* feature */
.feature-title{left:96px;top:6px;font-size:38px;color:var(--ink);letter-spacing:-.5px;white-space:nowrap}
.feature-title small{font-size:26px}
.rule{height:2px;background:var(--rule)}
.slider-arrows{left:654px;top:25px}
.partner-logo{left:96px;top:90px;width:141px;height:132px;background:#fff;border:2px solid #cfcfcf;display:flex;align-items:center;justify-content:center;text-align:center;font-size:15px;font-weight:500;color:var(--orange);line-height:1.2}
.feature-text{left:260px;top:90px;width:440px;font-size:15px;line-height:26px}
.btn{display:flex;align-items:center;justify-content:center;gap:14px;height:34px;border-radius:4px;color:#fff;font-weight:700;font-size:16px;text-shadow:0 1px 1px rgba(0,0,0,.35)}
.btn-orange{background:linear-gradient(var(--orange-light),var(--orange))}
.btn-navy{background:linear-gradient(var(--navy-light),var(--navy))}
.btn svg{flex:none}

/* news */
.column-shadow{left:716px;top:0;width:24px;height:310px;background:linear-gradient(90deg,rgba(0,0,0,0),rgba(0,0,0,.05))}
.news-title{left:838px;top:-6px;font-size:42px;color:var(--orange)}
.news-item{left:777px;width:315px}
.news-item a{display:block;color:var(--navy);font-size:17px;font-weight:500;line-height:20px;text-decoration:none}
.news-item time{display:block;font-size:13px;color:#777;margin-top:4px}
.dash{border-top:1px dashed #999}

/* accreditation band */
.band{left:0;top:355px;width:1200px;height:107px;background:var(--band)}
.badge{top:380px;height:62px;background:#d9d9d9;border-radius:6px}
.badge.round{border-radius:50%}

/* footer */
.footer{left:0;top:462px;width:1200px;height:412px;background:linear-gradient(var(--footer-top),var(--footer-bottom) 45%);border-top:1px solid #555;color:var(--footer-text)}
.world-map{left:440px;top:100px;width:420px;height:270px;background:radial-gradient(ellipse at center,rgba(120,120,120,.28),rgba(60,60,60,.05) 70%,transparent);border-radius:40%}
.footer-head{font-size:24px;color:#fff;font-family:"Oswald",sans-serif;font-weight:300;letter-spacing:-.3px}
.subscribe{left:205px;top:38px;width:104px;height:31px;font-size:15px;letter-spacing:.5px}
.footer-small{font-size:13px}
.phone{left:782px;top:37px;font-family:"Oswald",sans-serif;font-weight:300;font-size:24px;color:#bdbdbd}
.social{top:39px;width:32px;height:32px;border-radius:50%;background:#555}
.social.active{background:#fff}
.brand{left:958px;top:82px;display:flex;align-items:center;gap:6px;font-size:24px;color:#c7c7c7;font-weight:500}
.brand i{width:22px;height:22px;border-radius:50%;border:2px solid #c7c7c7;display:block}
.fdash{left:98px;width:987px;border-top:1px dashed var(--footer-dash)}
.link-col{top:150px}
.link-col h3{font-family:"Oswald",sans-serif;font-weight:300;font-size:25px;color:#fff;margin-bottom:16px}
.link-col li{list-style:none;font-size:14px;color:#cfcfcf}
.copyright{left:102px;top:370px;font-size:12px;color:#cfcfcf}
.legal{right:116px;top:370px;font-size:12px;color:#cfcfcf}
</style>
</head>
<body>

<section class="feature">
  <h1 class="abs heading feature-title">Com.AU <small>-</small> It does what it says on box</h1>
  <div class="abs rule" style="left:96px;top:64px;width:599px"></div>
  <svg class="abs slider-arrows" width="36" height="24" viewBox="0 0 36 24" aria-label="Previous and next">
    <polygon points="14,0 14,24 0,12" fill="var(--navy)"/>
    <polygon points="20,0 20,24 34,12" fill="var(--navy)"/>
  </svg>
  <div class="abs partner-logo">Aurel Domain<br>Authority</div>
  <p class="abs feature-text">.AUstralia's home on the Internet - COM.AU is trusted by users around the world due to the strict registration policies which maintain the integrity &amp; accuracy of the entire .AU namespace. With over 2+ million registrations, .COM.AU is the best domain to help your business reach the Australian audience.</p>
  <a class="abs btn btn-orange" style="left:97px;top:255px;width:288px">Register your .COM.AU Today!
    <svg width="14" height="10" viewBox="0 0 14 10"><polygon points="0,0 14,0 7,10" fill="#fff"/></svg></a>
  <a class="abs btn btn-navy" style="left:399px;top:255px;width:142px">Read More
    <svg width="14" height="10" viewBox="0 0 14 10"><polygon points="0,0 14,0 7,10" fill="#fff"/></svg></a>
</section>

<section class="news">
  <div class="abs column-shadow"></div>
  <svg class="abs" style="left:777px;top:10px" width="42" height="34" viewBox="0 0 42 34" aria-label="News">
    <rect x="4" y="4" width="34" height="26" rx="3" fill="none" stroke="var(--orange)" stroke-width="2.5"/>
    <line x1="10" y1="12" x2="32" y2="12" stroke="var(--orange)" stroke-width="2.5"/>
    <line x1="10" y1="18" x2="32" y2="18" stroke="var(--orange)" stroke-width="2"/>
    <line x1="10" y1="23" x2="26" y2="23" stroke="var(--orange)" stroke-width="2"/>
  </svg>
  <h2 class="abs heading news-title">Latest News</h2>
  <div class="abs rule" style="left:777px;top:64px;width:311px"></div>
  <article class="abs news-item" style="top:86px">
    <a>Velquor Corporation Announces .CO Accreditation -</a>
    <time>April 13, 2012</time>
  </article>
  <div class="abs dash" style="left:781px;top:158px;width:307px"></div>
  <article class="abs news-item" style="top:169px">
    <a>Velquor Attracts Leading Senior Channel Manager Marisa Delton</a>
    <time>April 13, 2012</time>
  </article>
  <div class="abs dash" style="left:781px;top:236px;width:307px"></div>
  <a class="abs btn btn-orange" style="left:773px;top:255px;width:138px">Read More
    <svg width="14" height="10" viewBox="0 0 14 10"><polygon points="0,0 14,0 7,10" fill="#fff"/></svg></a>
</section>

<section class="accreditations" aria-label="Accreditations">
  <div class="abs band"></div>
  <svg class="abs" style="left:0;top:348px" width="1200" height="10" viewBox="0 0 1200 10" preserveAspectRatio="none">
    <polyline points="0,8 10,2 20,8 30,2 40,8 50,2 60,8 70,2 80,8 90,2 100,8 110,2 120,8 130,2 140,8 150,2 160,8 170,2 180,8 190,2 200,8 210,2 220,8 230,2 240,8 250,2 260,8 270,2 280,8 290,2 300,8 310,2 320,8 330,2 340,8 350,2 360,8 370,2 380,8 390,2 400,8 410,2 420,8 430,2 440,8 450,2 460,8 470,2 480,8 490,2 500,8 510,2 520,8 530,2 540,8 550,2 560,8 570,2 580,8 590,2 600,8 610,2 620,8 630,2 640,8 650,2 660,8 670,2 680,8 690,2 700,8 710,2 720,8 730,2 740,8 750,2 760,8 770,2 780,8 790,2 800,8 810,2 820,8 830,2 840,8 850,2 860,8 870,2 880,8 890,2 900,8 910,2 920,8 930,2 940,8 950,2 960,8 970,2 980,8 990,2 1000,8 1010,2 1020,8 1030,2 1040,8 1050,2 1060,8 1070,2 1080,8 1090,2 1100,8 1110,2 1120,8 1130,2 1140,8 1150,2 1160,8 1170,2 1180,8 1190,2 1200,8 1200,10 0,10" fill="var(--band)" stroke="#dcdcdc"/>
  </svg>
  <svg class="abs" style="left:98px;top:397px" width="22" height="28" viewBox="0 0 22 28"><polyline points="18,2 5,14 18,26" fill="none" stroke="#999" stroke-width="5"/></svg>
  <div class="abs badge" style="left:144px;width:70px"></div>
  <div class="abs badge round" style="left:254px;width:74px"></div>
  <div class="abs badge" style="left:368px;width:100px"></div>
  <div class="abs badge" style="left:508px;width:88px;top:396px;height:32px"></div>
  <div class="abs badge round" style="left:636px;width:62px"></div>
  <div class="abs badge" style="left:738px;width:57px;height:66px"></div>
  <div class="abs badge round" style="left:838px;width:72px"></div>
  <div class="abs badge" style="left:952px;width:80px"></div>
  <svg class="abs" style="left:1066px;top:397px" width="22" height="28" viewBox="0 0 22 28"><polyline points="4,2 17,14 4,26" fill="none" stroke="var(--orange)" stroke-width="5"/></svg>
</section>

<footer class="abs footer">
  <div class="abs world-map" role="img" aria-label="Dotted world map"></div>

  <h3 class="abs footer-head" style="left:100px;top:36px">Mailing List</h3>
  <a class="abs btn btn-orange subscribe">SUBSCRIBE</a>
  <p class="abs footer-small" style="left:100px;top:79px">Be alerted about breakthrough</p>

  <h3 class="abs footer-head" style="left:661px;top:39px">Contact Us</h3>
  <svg class="abs" style="left:766px;top:46px" width="9" height="15" viewBox="0 0 9 15" aria-label="Phone"><rect x="0.5" y="0.5" width="8" height="14" rx="2" fill="#ddd"/><rect x="2" y="2.5" width="5" height="6" fill="#222"/></svg>
  <p class="abs phone">+1.5550142763</p>
  <svg class="abs" style="left:764px;top:76px" width="15" height="12" viewBox="0 0 15 12" aria-label="Chat"><ellipse cx="7.5" cy="5" rx="7" ry="4.5" fill="#ddd"/><polygon points="3,8 2,12 7,9" fill="#ddd"/></svg>
  <p class="abs footer-small" style="left:785px;top:73px">Chat with us</p>

  <span class="abs social active" style="left:934px"></span>
  <span class="abs social" style="left:972px"></span>
  <span class="abs social" style="left:1010px"></span>
  <span class="abs social" style="left:1048px"></span>
  <div class="abs brand"><i></i>Velquor</div>

  <div class="abs fdash" style="top:123px"></div>

  <nav class="abs link-col" style="left:101px">
    <h3>Domain</h3>
    <ul style="line-height:30px">
      <li>Name Registration</li><li>Name Services</li><li>New Top Level Domains</li><li>International Phone Numbers</li>
    </ul>
  </nav>
  <nav class="abs link-col" style="left:304px;top:148px">
    <h3>Hosting</h3>
    <ul style="line-height:30px;margin-left:2px">
      <li>Web Hosting Packages</li><li>Email Hosting Packages</li><li>Customer Login</li>
    </ul>
  </nav>
  <nav class="abs link-col" style="left:504px">
    <h3>Resellers</h3>
    <ul style="line-height:24px;margin-left:2px">
      <li>API Solution</li><li>Reseller Support</li><li>Signup</li>
    </ul>
  </nav>
  <nav class="abs link-col" style="left:704px">
    <h3>About Velquor</h3>
    <ul style="line-height:24px;margin-left:-3px">
      <li>Our Company</li><li>Our People</li><li>Our Technology</li>
    </ul>
  </nav>
  <nav class="abs link-col" style="left:916px;top:148px">
    <h3>Quick Support</h3>
    <ul style="line-height:24px;margin-left:-1px">
      <li>Domain Support</li><li>DNS Support</li><li>Hosting Support</li>
    </ul>
  </nav>

  <div class="abs fdash" style="top:344px"></div>
  <p class="abs copyright">Copyright © 2012-2014 Velquor Corporation All Rights Reserved.</p>
  <p class="abs legal">Contact Us | FAQ | Privacy Policy | Terms of Services | Sitemap</p>
</footer>

</body>
</html>
```